Business Card Design Project

We need a business card for a new technology services company. We develop software and implement software packages for our business customers and although we will begin with just one or two service offerings, our service offerings will expand over time. Our name comes from the an author, KL Barrow, and his "idea" was that opportunity should be based on ability and achievement, not on social status.

We would like to see a design that is standard in its size and shape, but stands apart in its dramatic color contrasts. The card should not use too many colors - the colors used in the background should highlight the brilliant blues of the logo (see attachment) to dramatic effect. The background should not be white.

If necessary, you can change the color of the words "KL Barrow", but not the word "Idea".

Card size should be U.S. standard 2 inches by 3.5 inches and provide for 1/8 inch bleed area on each side.

We need a design for both sides of the business card, one side communicating the company logo and contact information, the other side being purely graphical, incorporating the logo but no other information.

Contact Information Required:
Kate Brook
KateBrook@klbarrowvista.com
614-387-2259

Target Market(s)

Business executives

Industry/Entity Type

Software

Requirements
Must have
• It must have the full company logo on one side, and at least the graphic element of the logo on the other. Either that or the full logo on both.
Nice to have
• It would be nice to have a design that could work without needing two different textures. For example, it would be nice if the entire card could be shiny, not just parts of the card.

It would also be nice if texture is something we could add later.
Should not have
• The card should not use the color green.

```html
<!DOCTYPE html>
<html lang="en">
<head>
<meta charset="utf-8">
<title>KL Barrow Vista — Business Card, Front and Back</title>
<link rel="stylesheet" href="https://fonts.googleapis.com/css2?family=Roboto:wght@300;400;700&display=swap">
<style>
  :root {
    --page: #e8e6e3;
    --card-dark: #2a2a2b;
    --card-darker: #1d1d1e;
    --card-light: #3a3a3c;
    --brand-blue: #1a9ddb;
    --brand-blue-deep: #0d7fc0;
    --silver: #a9abae;
    --ink-white: #f4f6f8;
  }
  * { box-sizing: border-box; margin: 0; padding: 0; }
  html, body {
    width: 1200px;
    height: 750px;
    overflow: hidden;
    background: var(--page);
    font-family: "Roboto", Arial, sans-serif;
  }
  .sheet {
    position: relative;
    width: 1200px;
    height: 750px;
  }
  .card {
    position: absolute;
    top: 221px;
    width: 540px;
    height: 309px;
    border-radius: 20px;
    overflow: hidden;
    box-shadow: 0 10px 28px rgba(0, 0, 0, 0.28);
  }
  .card--front { left: 40px; }
  .card--back { left: 620px; }
  .card__texture {
    position: absolute;
    inset: 0;
    background: radial-gradient(ellipse at 40% 35%, var(--card-light) 0%, var(--card-dark) 55%, var(--card-darker) 100%);
  }
  .wordmark {
    position: absolute;
    display: flex;
    align-items: center;
    gap: 12px;
    font-weight: 300;
    color: var(--brand-blue);
    letter-spacing: -0.02em;
    white-space: nowrap;
  }
  .wordmark__dot {
    display: block;
    border-radius: 50%;
    background: var(--brand-blue);
    flex: none;
  }
  .card--front .wordmark {
    left: 52px;
    top: 76px;
    font-size: 40px;
  }
  .card--front .wordmark__dot { width: 22px; height: 22px; }
  .contact {
    position: absolute;
    left: 74px;
    top: 148px;
    list-style: none;
    color: var(--ink-white);
    font-size: 13.5px;
    font-weight: 400;
    z-index: 2;
  }
  .contact__item {
    display: flex;
    align-items: center;
    gap: 8px;
    height: 22px;
    white-space: nowrap;
  }
  .contact__icon { width: 11px; height: 11px; flex: none; }
  .swoosh {
    position: absolute;
    inset: 0;
    width: 540px;
    height: 309px;
  }
  .holder-name {
    position: absolute;
    right: 32px;
    top: 204px;
    color: var(--ink-white);
    font-weight: 700;
    font-size: 19px;
    letter-spacing: 0.01em;
    white-space: nowrap;
  }
  .card--back .wordmark {
    left: 50%;
    top: 50%;
    transform: translate(-50%, -50%);
    font-size: 52px;
  }
  .card--back .wordmark__dot { width: 28px; height: 28px; }
</style>
</head>
<body>
<main class="sheet">

  <section class="card card--front" aria-label="Business card front">
    <div class="card__texture" role="img" aria-label="Dark charcoal card surface with a subtle tonal damask texture"></div>

    <div class="wordmark">
      <span class="wordmark__name">KLBarrowVista</span>
      <span class="wordmark__dot"></span>
    </div>

    <svg class="swoosh" viewBox="0 0 540 309" aria-hidden="true">
      <defs>
        <linearGradient id="band-fill" x1="0" y1="0" x2="1" y2="0">
          <stop offset="0" stop-color="var(--brand-blue)"/>
          <stop offset="1" stop-color="var(--brand-blue-deep)"/>
        </linearGradient>
      </defs>
      <path d="M0,262 C120,264 210,246 300,212 C390,178 460,160 540,160 L540,170 C460,170 390,188 300,222 C210,256 120,274 0,272 Z" fill="var(--silver)"/>
      <path d="M0,278 C120,280 210,262 300,228 C390,194 460,176 540,176 L540,309 L0,309 Z" fill="url(#band-fill)"/>
    </svg>

    <ul class="contact">
      <li class="contact__item">
        <svg class="contact__icon" viewBox="0 0 12 12" aria-hidden="true">
          <circle cx="6" cy="6" r="6" fill="var(--brand-blue)"/>
          <path d="M3.8 3.2 L5 3 L5.5 4.6 L4.8 5.2 Q5.5 6.6 6.8 7.2 L7.4 6.5 L9 7 L8.8 8.2 Q5.5 8.6 3.8 3.2 Z" fill="var(--ink-white)"/>
        </svg>
        <span>614-387-2259</span>
      </li>
      <li class="contact__item">
        <svg class="contact__icon" viewBox="0 0 12 12" aria-hidden="true">
          <circle cx="6" cy="6" r="6" fill="var(--brand-blue)"/>
          <rect x="3" y="4" width="6" height="4.2" fill="var(--ink-white)"/>
          <path d="M3 4 L6 6.4 L9 4" fill="none" stroke="var(--brand-blue)" stroke-width="0.7"/>
        </svg>
        <span>KateBrook@klbarrowvista.com</span>
      </li>
    </ul>

    <p class="holder-name">KATE BROOK</p>
  </section>

  <section class="card card--back" aria-label="Business card back">
    <div class="card__texture" role="img" aria-label="Dark charcoal card surface with a subtle tonal damask texture"></div>
    <div class="wordmark">
      <span class="wordmark__name">KLBarrowVista</span>
      <span class="wordmark__dot"></span>
    </div>
  </section>

</main>
</body>
</html>
```